KRL Stationery Design Project

Dear Designers,
We need a new stationery design for company to match our new logo.
Designers should provide a design for the following:
1. Business Card: 3.5x2 Inches.
2. Letterhead: A4 size.
3. Envelops: 25x35.5 Cm.
You can keep the Arabic name at the bottom of the logo Or you can use the separate attached Arabic Name.
Please refer to the attached logo guide for design information.
Sample Business Card information:
Name: Tarek Sowan
Position: Operation Manager
Tel: +966 920007164 Ex. 500
Fax: +966 (3)8842617
Mob: +966 (5)00263817
email: tarek@krl-example.com.sa
URL: www.krl-example.com.sa
Address:
Nakheel Heights, Suite 718
Zayed bin Omar Str.
Khobar, 31847
Saudi Arabia
Updates
Dear All,
Please note, we had uploaded our logo along with Arabic writing in Adobe illustrator format (.ai).
Regards,
Karim
Dear All,
A sample data for the business card had been added as per your request.
Regards,
Karim

```html
<!DOCTYPE html>
<html lang="en">
<head>
<meta charset="utf-8">
<title>KRL Business Card</title>
<link href="https://fonts.googleapis.com/css2?family=Open+Sans:ital,wght@0,400;0,700;1,700&display=swap" rel="stylesheet">
<style>
  :root {
    --navy: #0f2f52;
    --grey-line: #a9a9a9;
    --text: #3a3a3a;
    --card: #ffffff;
    --backdrop: #222326;
  }
  * { margin: 0; padding: 0; box-sizing: border-box; }
  html, body {
    width: 960px;
    height: 1200px;
    overflow: hidden;
    background: var(--backdrop);
    font-family: "Open Sans", Arial, sans-serif;
  }
  .card {
    position: absolute;
    left: 60px;
    width: 840px;
    height: 480px;
    background: var(--card);
    border-radius: 30px;
    overflow: hidden;
  }
  .card--front { top: 75px; }
  .card--back { top: 625px; left: 57px; }
  .card__swoosh {
    position: absolute;
    inset: 0;
    width: 840px;
    height: 480px;
  }
  .brand {
    position: absolute;
    left: 0;
    right: 0;
    display: flex;
    justify-content: center;
    align-items: center;
    gap: 22px;
    color: var(--navy);
    font-weight: 700;
    letter-spacing: 4px;
  }
  .brand__dot {
    border-radius: 50%;
    background: var(--navy);
  }
  .card--front .brand { top: 130px; font-size: 110px; line-height: 1; }
  .card--front .brand__dot { width: 34px; height: 34px; }
  .card--back .brand { top: 160px; font-size: 140px; line-height: 1; }
  .card--back .brand__dot { width: 42px; height: 42px; }
  .contact {
    position: absolute;
    left: 0;
    right: 0;
    top: 298px;
    text-align: center;
    color: var(--text);
    font-size: 19px;
    line-height: 38px;
  }
  .contact__name { color: var(--navy); font-size: 25px; }
  .contact__role { color: var(--navy); font-size: 19px; }
  .contact__label { font-weight: 700; font-style: italic; }
  .contact__sep { margin: 0 8px; }
</style>
</head>
<body>
  <section class="card card--front">
    <svg class="card__swoosh" viewBox="0 0 840 480" aria-hidden="true">
      <path d="M705 0 L840 0 L840 150 C815 75 770 25 705 0 Z" fill="var(--navy)"/>
      <path d="M690 0 C765 25 818 85 832 165" fill="none" stroke="var(--grey-line)" stroke-width="4"/>
      <path d="M0 340 C25 410 65 455 120 480 L0 480 Z" fill="var(--navy)"/>
      <path d="M0 325 C20 400 70 460 130 480" fill="none" stroke="var(--grey-line)" stroke-width="4"/>
    </svg>
    <div class="brand"><span class="brand__dot"></span><span>KRL</span></div>
    <div class="contact">
      <p><span class="contact__name">Your Name - </span><span class="contact__role">Designation</span></p>
      <p><span class="contact__label">t</span> : 123-123-1234<span class="contact__sep">|</span><span class="contact__label">f</span> : 123-123-1234</p>
      <p><span class="contact__label">e</span> : info@krl-example.com<span class="contact__sep">|</span><span class="contact__label">w</span> : www.krl-example.com</p>
      <p>1234, Suite# 123, Street Name, Country Code</p>
    </div>
  </section>

  <section class="card card--back">
    <div class="brand"><span class="brand__dot"></span><span>KRL</span></div>
  </section>
</body>
</html>
```